Wordpress Website for Waikiki based Boutique Retail Commercial Realestate Company

Aloha!
We need a wordpress design for a new company based in Waikiki, Oahu. I am an experienced real estate professional leaving a large national firm to open a boutique agency. I have several colleagues that work for these type of boutique companies on the mainland - and all seemingly have similar type Wordpress websites. Below are the examples I'd like you to use as a starting point but I would like to differentiate ourselves because of our unique position of being located on a tropical island. The design should communicate elegance, sophistication, experience and market knowledge. The photos should all be of Hawaii and Waikiki.

Here are the websites I'd like this to be similar to (but smaller since I am currently a one woman company):
http://www.plv.example/
http://marlowgrangepartners.example/
http://www.brennickfolk.example/
(this one is residential real estate, which I don't do but still like this look): http://www.coralnestedhome.example/

I am not that tech savy but I do own my domain, have it hosted and have had the hosting company install the necessary Wordpress component on to the account.

I would like to form a relationship with a designer that can grow with me so as I want to add features in the future, I can continue to hire you. If you are strictly a designer, that is ok, but I am also looking for someone to do regular administrative work on the website by uploading new information to it regularly.

Also, would you advise me on how to "upload" it to the hosting company?

Aloha Designers,

Here are examples of the interactive map that I'd like to do for my living resume. Instead of an image, however, I'd like it to be over an aerial from Google Earth of Waikiki:

http://www.gildedpalmarcade.example/
http://www.sunlineboardpath.example/

Hope this answers some questions. I look forward to your designs! Mahalo, Marisol

Target Market(s)

upscale & luxury retailers as well as owners of property in Waikiki

Industry/Entity Type

Real Estate

Requirements
Must have
• I need to have the web page coded so I can upload and have a working live web page.

Here is the unique element I'd like to have on my webpage:

I'd like to have a map of Waikiki (Google earth image) that has roll-overs on it. This will be my living, breathing resume. So when someone visits my website, they can roll-over the map and the name of a property will pop-up. They can expand on it to learn more about the work I've done on that property. Don't worry, I'll provide you will all the detail but I'd like to see a sample of how you would handle this.

The only design idea that I've had or thought to play with would be to have the website all in shades of grey except for whatever is being featured - so if there is a large photo - everything would be grey except for the subject building. I don't know if there is an easy Photoshop or software way to do this, and if not, then skip the idea because it would be too labor intensive for lots of photos.

Below is all the typical pages a company like me would have:
Landing Page - full photo images
Assignments/Listings Page
Services Page - this page might have the map described above
News Page
(I'd like to be able to either have this connect to RSS/Twitter/FB. I basically want to take local news articles and upload them here. I will also have an admin person email blast these to my clients once a week in the future. I need some capture system here for people to sign up to receive the news by email, sign up to receive available listings or sign up to participate in future surveys of Waikiki- I'm about to launch one in a week or two).

Contact Page
Nice to have
• Client Access Only Page-
With this page, I'd like to have the ability to control who has access to this page.

It should require their email and password.
It should show the files in PDF format (like the link below)
It should allow them to download the file.
It should send me an email every time someone access this Client Page.

http://www.tidecrestmarket.example/catalog-leasing-2011.html

```html
<!DOCTYPE html>
<html lang="en">
<head>
<meta charset="utf-8">
<title>Halden Reyes &amp; Co</title>
<link rel="stylesheet" href="https://fonts.googleapis.com/css2?family=Roboto+Condensed:wght@400;700&display=swap">
<style>
  :root {
    --ink: #0b0b0b;
    --bar: #161616;
    --panel: #1b1b1b;
    --text: #ffffff;
    --muted: #9a9a9a;
    --accent: #c8101a;
    --divider: #3a3a3a;
  }
  * { margin: 0; padding: 0; box-sizing: border-box; }
  html, body { width: 1200px; height: 720px; overflow: hidden; background: var(--ink); }
  body { font-family: "Roboto Condensed", Arial, sans-serif; color: var(--text); position: relative; }

  .hero-photo {
    position: absolute; left: 0; top: 80px; width: 1200px; height: 640px;
    background:
      linear-gradient(180deg, rgba(20,30,90,0.0) 0%, rgba(0,0,0,0) 40%),
      radial-gradient(ellipse at 20% 70%, #6b5a1e 0%, rgba(60,60,20,0) 45%),
      radial-gradient(ellipse at 80% 30%, #1f2f8a 0%, rgba(20,30,90,0) 55%),
      linear-gradient(180deg, #26307a 0%, #2f3a5a 30%, #2c3a22 60%, #1e2a18 85%, #171d14 100%);
  }

  .site-header {
    position: absolute; left: 0; top: 0; width: 1200px; height: 80px;
    background: linear-gradient(180deg, #1f1f1f 0%, #050505 100%);
  }
  .brand {
    position: absolute; left: 121px; top: 0; width: 168px; height: 138px;
    background: var(--ink);
    display: flex; flex-direction: column; align-items: center; justify-content: flex-end;
    padding-bottom: 12px;
  }
  .brand-mark { width: 56px; height: 56px; border-radius: 50%; background: #8c8c8c; margin-bottom: 22px; }
  .brand-name { font-size: 17px; font-weight: 400; color: #c9c9c9; }

  .main-nav { position: absolute; top: 0; left: 448px; height: 80px; display: flex; align-items: flex-start; }
  .main-nav a {
    color: var(--text); text-decoration: none; font-size: 15px; text-transform: uppercase;
    padding: 31px 29px 0; height: 56px; border-right: 1px solid var(--divider); margin-top: 10px;
    line-height: 1; padding-top: 21px;
  }
  .main-nav a:last-child { border-right: none; }
  .nav-glow {
    position: absolute; left: 460px; top: 70px; width: 70px; height: 12px; border-radius: 50%;
    background: radial-gradient(ellipse, rgba(230,20,20,0.95) 0%, rgba(200,16,26,0) 70%);
  }

  .hero-copy { position: absolute; left: 141px; top: 196px; }
  .hero-title { font-size: 44px; font-weight: 400; line-height: 1; text-transform: uppercase; text-shadow: 0 2px 4px rgba(0,0,0,.5); }
  .hero-lede { margin-top: 24px; font-size: 22px; line-height: 29px; text-shadow: 0 1px 3px rgba(0,0,0,.6); }

  .slide-arrow { position: absolute; top: 330px; width: 24px; height: 62px; }
  .slide-arrow.prev { left: 66px; }
  .slide-arrow.next { left: 1110px; }

  .feature-bar {
    position: absolute; left: 145px; top: 386px; width: 910px; height: 40px;
    background: var(--panel); border-left: 5px solid var(--accent);
    font-size: 18px; text-transform: uppercase; padding: 10px 0 0 13px;
  }

  .listing-card { position: absolute; top: 441px; width: 220px; height: 190px; }
  .listing-photo { height: 140px; }
  .listing-label {
    height: 50px; background: var(--panel); border-left: 5px solid var(--accent);
    display: flex; align-items: center; justify-content: space-between;
    padding: 0 11px 0 15px; font-size: 17px; text-transform: uppercase;
  }
  .photo-a { background: linear-gradient(180deg, #4f86d8 0%, #a9c4e2 35%, #d8d6cf 60%, #3fb8c4 85%, #2a9aa0 100%); }
  .photo-b { background: linear-gradient(180deg, #5a8fd6 0%, #b8cde3 30%, #6b7a62 55%, #e4dcc8 75%, #37b5c4 100%); }
  .photo-c { background: linear-gradient(180deg, #6f98cf 0%, #9a7658 35%, #c8aa82 60%, #6a5a42 100%); }
  .photo-d { background: linear-gradient(180deg, #2f73cf 0%, #e4dca8 40%, #c9c090 65%, #2d6fa0 100%); }

  .site-footer {
    position: absolute; left: 0; top: 670px; width: 1200px; height: 50px;
    background: rgba(40,40,40,0.88);
  }
  .legal { position: absolute; left: 145px; top: 19px; font-size: 11px; font-weight: 700; color: var(--muted); text-transform: uppercase; }
  .social { position: absolute; left: 908px; top: 14px; display: flex; gap: 6px; }
  .social span { width: 22px; height: 22px; border-radius: 50%; background: #8a8a8a; display: block; }
</style>
</head>
<body>
  <div class="hero-photo" role="img" aria-label="Night view of Waikiki hotels, palm trees, a lit pool and Diamond Head across the bay"></div>

  <header class="site-header">
    <div class="brand">
      <span class="brand-mark"></span>
      <span class="brand-name">Halden Reyes &amp; Co</span>
    </div>
    <nav class="main-nav">
      <a href="#">Home</a>
      <a href="#">About</a>
      <a href="#">Services</a>
      <a href="#">Gallery</a>
      <a href="#">Blog</a>
      <a href="#">Contact</a>
    </nav>
    <div class="nav-glow"></div>
  </header>

  <section class="hero-copy">
    <h1 class="hero-title">Welcome to Halden Reyes &amp; Co</h1>
    <p class="hero-lede">eiusmod tempor incididunt ut labore et dolore magna aliqua.<br>Ut enim ad minim veniam, quis nostrud</p>
  </section>

  <svg class="slide-arrow prev" viewBox="0 0 24 62"><polyline points="22,2 3,31 22,60" fill="none" stroke="#cfcfcf" stroke-width="2"/></svg>
  <svg class="slide-arrow next" viewBox="0 0 24 62"><polyline points="2,2 21,31 2,60" fill="none" stroke="#cfcfcf" stroke-width="2"/></svg>

  <h2 class="feature-bar">Feature Listing</h2>

  <article class="listing-card" style="left:145px">
    <div class="listing-photo photo-a" role="img" aria-label="Waikiki beachfront towers with turquoise water"></div>
    <div class="listing-label">Doloremque <svg width="20" height="20" viewBox="0 0 20 20"><circle cx="10" cy="10" r="9" fill="none" stroke="#9a9a9a" stroke-width="1.5"/><path d="M10 5v10M5 10h10" stroke="#9a9a9a" stroke-width="1.5"/></svg></div>
  </article>
  <article class="listing-card" style="left:375px">
    <div class="listing-photo photo-b" role="img" aria-label="Beach hotel tower with Diamond Head and the shoreline behind"></div>
    <div class="listing-label">Laudantium <svg width="20" height="20" viewBox="0 0 20 20"><circle cx="10" cy="10" r="9" fill="none" stroke="#9a9a9a" stroke-width="1.5"/><path d="M10 5v10M5 10h10" stroke="#9a9a9a" stroke-width="1.5"/></svg></div>
  </article>
  <article class="listing-card" style="left:605px">
    <div class="listing-photo photo-c" role="img" aria-label="Open-air pavilion with pergola and stone terrace"></div>
    <div class="listing-label">Doloremque <svg width="20" height="20" viewBox="0 0 20 20"><circle cx="10" cy="10" r="9" fill="none" stroke="#9a9a9a" stroke-width="1.5"/><path d="M10 5v10M5 10h10" stroke="#9a9a9a" stroke-width="1.5"/></svg></div>
  </article>
  <article class="listing-card" style="left:835px">
    <div class="listing-photo photo-d" role="img" aria-label="Lifeguard tower on the beach with Diamond Head in the distance"></div>
    <div class="listing-label">Laudantium <svg width="20" height="20" viewBox="0 0 20 20"><circle cx="10" cy="10" r="9" fill="none" stroke="#9a9a9a" stroke-width="1.5"/><path d="M10 5v10M5 10h10" stroke="#9a9a9a" stroke-width="1.5"/></svg></div>
  </article>

  <footer class="site-footer">
    <p class="legal">© 2013 Halden Reyes &amp; Co.All Rights Reserved | Privacy | T&amp;C</p>
    <div class="social" aria-label="Social links">
      <span></span><span></span><span></span><span></span><span></span><span></span>
    </div>
  </footer>
</body>
</html>
```